I am starting a company that will help small businesses that are looking to raise money over the internet (i.e. crowd fund) in reliance of the JOBS Act and the new rules that have been recently passed.

Initially, the website will help a business figure out if it is qualified to raise money and if so, it will tell the business what information is required.

The various pages will need to gather information from the businesses through Yes/No questionnaires, drop-down lists and free text boxes -

I am still thinking about my company's name and don't have a logo - for now, please use the name "MLAH (marble lantern advisory hub)" - feel free to throw in an idea for a logo

Hi all - I was wondering if I could get some design suggestions that don't use stock photos- thanks

Based on the designs I have received so far, I don't think the description of my website is clear.  The website will NOT be a crowdfunding portal (i.e. it is not like plumvesta etc.)  It is an information website that will allow companies to determine if they are legally able to raise money online. 

If they are able to raise money online, then the company can sign-up for some paid services which include legal documents and agreements.

To help the design process, I've uploaded a draft of the questions that a company will need to answer to determine if it is able to raise money online.

The submitted designs should be for both the homepage as well as the pages on which the questions will be set out.

Thanks for taking the time to read.

small businesses that will be looking to raise money through crowd funding

Internet

• I need designs for the following pages:

1. Home page
- should be simple - links to 'about' page and 'blog' page
- room at the bottom for affiliate links/logos
- convey the message that there are many rules that need to be followed to legally crowd fund a company but that this website makes compliance easy
- prominent 'get started' button

2. Company questions pages
- laid out to ask ~ 5 questions:
- name of company (free text answer)
- amount raised in prior 12 months (drop down box)
- state of formation (drop down box)
- registered with the ODV (y/n)
- registered as an investment company (y/n)

- needs to be a help 'icon' beside the questions so that user can hover over the icon and get more information as to what the question is asking

3. Eligibility questions page
- list of ~25 questions (y/n) answers
-
4. Fund raising objectives page
- list of ~15 questions answers
- answers will be y/n, multiple choice, drop down menu or free text

5. Results page
- if company is not-eligible to proceed, display "Not Eligible" page with list of reasons why
- if company is eligible, display "Congratulations" page with link to "Sign-up and Continue"

6. Sign-up page
- name
- address
- e-mail etc.
- check box to agree to terms and conditions

7. 'blog' page

8. about / disclaimer page

```html
<!DOCTYPE html>
<html lang="en">
<head>
<meta charset="utf-8">
<title>MLAH – Marble Lantern Advisory Hub</title>
<link href="https://fonts.googleapis.com/css2?family=Open+Sans:wght@400;600;700&display=swap" rel="stylesheet">
<style>
:root{
  --orange:#f6a01a;
  --blue:#1f6fb2;
  --blue-footer:#2b73b6;
  --blue-bar:#1f5f9c;
  --blue-deep:#1d4f86;
  --green:#6bb13f;
  --ink:#4a4a4a;
  --muted:#8c8c8c;
  --line:#e3e3e3;
  --band:#ededed;
  --dark:#333436;
  --white:#ffffff;
}
*{margin:0;padding:0;box-sizing:border-box}
html,body{width:1200px;height:3032px;overflow:hidden}
body{font-family:"Open Sans",Arial,sans-serif;color:var(--ink);background:var(--white)}
.wrap{width:840px;margin:0 auto;position:relative}

/* header */
.site-header{height:72px;border-bottom:1px solid var(--line)}
.site-header .inner{width:1136px;margin:0 auto;height:72px;display:flex;align-items:center}
.brand{display:flex;align-items:center;gap:10px;font-weight:700;font-size:26px;color:var(--blue)}
.brand-dot{width:22px;height:22px;border-radius:50%;background:var(--blue)}
.main-nav{display:flex;gap:44px;margin-left:300px;font-size:12px;font-weight:600;color:var(--muted);text-transform:uppercase}
.header-actions{margin-left:auto;display:flex;gap:14px}
.btn-small{background:var(--orange);color:var(--white);font-size:12px;font-weight:600;padding:8px 22px;border-radius:2px}

/* hero */
.hero{height:508px;background:linear-gradient(90deg,#f4f4f2 0%,#e9e7e3 40%,#d8cfc6 65%,#c6b7a6 100%);position:relative}
.hero-photo{position:absolute;right:0;top:0;width:640px;height:508px;background:radial-gradient(ellipse at 45% 40%,#e8d3b8 0%,#cbb59a 40%,#b59c84 75%,#a08a76 100%)}
.hero-copy{position:absolute;left:208px;top:170px;width:470px}
.hero-copy h1{font-weight:400;font-size:27px;line-height:1.15;color:var(--blue-deep)}
.hero-copy h1 strong{display:block;font-size:37px;font-weight:400;white-space:nowrap}
.hero-copy p{font-size:12px;line-height:1.6;margin-top:18px;color:#666;width:370px}
.btn-cta{display:inline-block;background:var(--orange);color:var(--white);font-size:20px;font-weight:600;padding:16px 48px;margin-top:28px;border-radius:2px}

/* welcome */
.welcome{height:380px;padding-top:28px}
.section-title{font-size:15px;font-weight:700;color:var(--blue);text-transform:uppercase}
.welcome-body{display:flex;gap:60px;margin-top:24px}
.video{width:300px;height:250px;background:linear-gradient(160deg,#cfd8e0,#9fb0bf 60%,#7d8b98);position:relative}
.video .play-bar{position:absolute;left:0;right:0;bottom:0;height:30px;background:rgba(0,0,0,.55)}
.video .play-icon{position:absolute;left:10px;bottom:8px;border-left:12px solid #fff;border-top:7px solid transparent;border-bottom:7px solid transparent}
.welcome-text{flex:1;font-size:12px;line-height:1.75;color:#777}
.meta-row{display:flex;justify-content:space-between;font-size:11px;color:var(--muted);margin-top:34px}
.meta-row .tag{color:var(--blue)}
.bar{height:5px;background:var(--line);margin-top:8px}
.bar span{display:block;height:100%;background:var(--green)}
.stats{display:flex;margin-top:10px;border:1px solid var(--line);width:220px}
.stats div{flex:1;text-align:center;padding:6px 0;font-size:10px;color:var(--muted);border-right:1px solid var(--line)}
.stats div:last-child{border-right:0}
.stats b{display:block;font-size:13px;color:var(--green)}

.divider{height:20px;background:var(--band);border-top:1px solid #ddd;border-bottom:1px solid #ddd}

/* guide cards */
.card-section{padding-top:30px}
.cards{display:flex;gap:18px;margin-top:20px}
.card{width:196px;font-size:10px;color:#888}
.card-img{height:120px}
.card h3{font-size:12px;font-weight:600;color:var(--blue);margin:10px 0 5px;white-space:nowrap}
.card p{line-height:1.55}
.card .meta-row{margin-top:10px;font-size:10px}
.card .stats{width:100%}
.stars{color:var(--orange);letter-spacing:1px}
.popular{height:420px}
.fresh{height:440px}

/* success */
.success{height:440px;padding-top:20px}
.success-box{display:flex;height:392px;background:var(--dark)}
.success-photo{width:420px;height:100%;background:linear-gradient(135deg,#55585c,#8a8d90 45%,#3f4144)}
.success-copy{flex:1;padding:40px 38px;color:#ccc;font-size:12px;line-height:1.7}
.success-copy h2{font-size:30px;font-weight:400;color:var(--white);margin-bottom:16px}
.success-copy p+p{margin-top:12px}
.success-copy .btn-cta{margin-top:30px;font-size:18px}

/* discover */
.discover{height:208px;margin-top:32px;background:linear-gradient(90deg,#d9d9d9,#c4c4c4 30%,#dcdcdc 55%,#bdbdbd 80%,#d4d4d4)}
.discover .wrap{height:208px;display:flex;align-items:center}
.discover-panel{background:rgba(255,255,255,.92);padding:26px 30px;width:560px}
.discover-panel h2{font-size:30px;font-weight:400;color:var(--blue);line-height:1.15}
.discover-panel p{font-size:16px;color:#777;margin-top:8px}
.connect-btn{margin-left:auto;display:flex;background:var(--blue-deep);color:var(--white);height:52px}
.connect-btn .name{font-size:22px;font-weight:700;padding:0 18px;display:flex;align-items:center;background:#2a5a98}
.connect-btn .label{font-size:12px;padding:0 16px;display:flex;align-items:center;white-space:nowrap}

/* social */
.social{height:192px;display:flex;align-items:center;justify-content:center;gap:40px}
.social h2{font-size:22px;font-weight:400;color:var(--blue)}
.social-icons{display:flex;gap:8px}
.social-icons span{width:40px;height:40px;display:block}

/* footer */
.site-footer{height:256px;background:var(--blue-footer);color:#d7e6f4;padding-top:32px}
.footer-cols{display:flex;justify-content:space-between}
.footer-cols h4{font-size:11px;font-weight:700;color:var(--white);text-transform:uppercase;margin-bottom:10px}
.footer-cols ul{list-style:none;font-size:11px;line-height:1.9}
.bottom-bar{height:32px;background:var(--blue-bar);color:#bcd3ea;font-size:10px;display:flex;align-items:center;justify-content:center}
</style>
</head>
<body>

<header class="site-header">
  <div class="inner">
    <div class="brand"><span class="brand-dot"></span>MLAH</div>
    <nav class="main-nav"><span>About</span><span>Blog</span><span>Guides</span></nav>
    <div class="header-actions"><span class="btn-small">Get started</span><span class="btn-small">Log in</span></div>
  </div>
</header>

<section class="hero">
  <div class="hero-photo" role="img" aria-label="Photo of a smiling small business owner"></div>
  <div class="hero-copy">
    <h1>sometimes by accident, <strong>sometimes on purpose</strong></h1>
    <p>Raising money online comes with many rules. Answer a few simple questions and we show you exactly what applies to your business.</p>
    <span class="btn-cta">Get started</span>
  </div>
</section>

<section class="welcome wrap">
  <h2 class="section-title">Welcome to marble lantern advisory hub</h2>
  <div class="welcome-body">
    <div class="video" role="img" aria-label="Video still of a woman working at a laptop"><div class="play-bar"></div><div class="play-icon"></div></div>
    <div class="welcome-text">
      <p>We are an information service, not a funding portal. We help small businesses learn whether they may legally raise funds online. Answer a short set of questions, see what the rules require, and get clear next steps. When you qualify, our paid services prepare the legal documents you need.</p>
      <div class="meta-row"><span class="tag">Eligibility check</span><span>About 10 minutes</span></div>
      <div class="bar"><span style="width:60%"></span></div>
      <div class="stats"><div><b>5</b>Steps</div><div><b>25</b>Questions</div></div>
    </div>
  </div>
</section>

<div class="divider"></div>

<section class="card-section popular wrap">
  <h2 class="section-title">Popular</h2>
  <div class="cards">
    <article class="card"><div class="card-img" role="img" aria-label="Photo of a family business team outdoors" style="background:linear-gradient(135deg,#8fb37a,#c9b48e)"></div><h3>Who May Raise Online?</h3><p>The basic tests a company must pass before it can offer shares on the internet.</p><div class="meta-row"><span class="tag">Eligibility</span><span class="stars">★★★★★</span></div><div class="bar"><span style="width:70%"></span></div><div class="stats"><div><b>8</b>Rules</div><div><b>4</b>Min read</div><div><b>2</b>Forms</div></div></article>
    <article class="card"><div class="card-img" role="img" aria-label="Photo of founders working together" style="background:linear-gradient(135deg,#d1a86f,#8e9f6a)"></div><h3>Limits Over 12 Months</h3><p>How much a business may raise in a year and what counts toward the total.</p><div class="meta-row"><span class="tag">Offering limits</span><span class="stars">★★★★★</span></div><div class="bar"><span style="width:55%"></span></div><div class="stats"><div><b>5</b>Rules</div><div><b>3</b>Min read</div><div><b>1</b>Forms</div></div></article>
    <article class="card"><div class="card-img" role="img" aria-label="Photo of two partners at a desk" style="background:linear-gradient(135deg,#c98a6a,#e2c3a0)"></div><h3>State of Formation</h3><p>Why the state where you formed your company matters for an online raise.</p><div class="meta-row"><span class="tag">Company facts</span><span class="stars">★★★★★</span></div><div class="bar"><span style="width:80%"></span></div><div class="stats"><div><b>6</b>Rules</div><div><b>5</b>Min read</div><div><b>3</b>Forms</div></div></article>
    <article class="card"><div class="card-img" role="img" aria-label="Photo of a meeting around a table" style="background:linear-gradient(135deg,#6f6a64,#b99a7c)"></div><h3>Disclosure Documents</h3><p>The information you must share with investors and when it must be filed.</p><div class="meta-row"><span class="tag">Paperwork</span><span class="stars">★★★★★</span></div><div class="bar"><span style="width:45%"></span></div><div class="stats"><div><b>9</b>Rules</div><div><b>6</b>Min read</div><div><b>4</b>Forms</div></div></article>
  </div>
</section>

<section class="success wrap">
  <div class="success-box">
    <div class="success-photo" role="img" aria-label="Photo of a mechanic working on a car engine"></div>
    <div class="success-copy">
      <h2>Success Stories</h2>
      <p>A small garage owner answered our questions in one afternoon, learned which rules applied, and had his legal documents ready within weeks. Clear answers replaced guesswork at every step of the process.</p>
      <p>Read how founders like him use simple checklists, plain language and ready documents to reach their goals while staying fully within the law.</p>
      <span class="btn-cta">Get started</span>
    </div>
  </div>
</section>

<div class="divider"></div>

<section class="card-section fresh wrap">
  <h2 class="section-title">New this week</h2>
  <div class="cards">
    <article class="card"><div class="card-img" role="img" aria-label="Photo of a car in a workshop" style="background:linear-gradient(135deg,#5d6f82,#a7b3bd)"></div><h3>Investment Company Test</h3><p>When a business counts as an investment company and why that blocks a raise.</p><div class="meta-row"><span class="tag">Eligibility</span><span class="stars">★★★★★</span></div><div class="bar"><span style="width:65%"></span></div><div class="stats"><div><b>4</b>Rules</div><div><b>3</b>Min read</div><div><b>1</b>Forms</div></div></article>
    <article class="card"><div class="card-img" role="img" aria-label="Photo of a modern office building" style="background:linear-gradient(135deg,#9fb7cf,#7d7a72)"></div><h3>Registering With ODV</h3><p>What prior registration means for your company and the questions we ask.</p><div class="meta-row"><span class="tag">Company facts</span><span class="stars">★★★★★</span></div><div class="bar"><span style="width:50%"></span></div><div class="stats"><div><b>3</b>Rules</div><div><b>4</b>Min read</div><div><b>2</b>Forms</div></div></article>
    <article class="card"><div class="card-img" role="img" aria-label="Photo of a bright shop interior" style="background:linear-gradient(135deg,#e2d2bd,#b9876a)"></div><h3>Setting Your Objectives</h3><p>Plan the amount, timing and type of offering that suits your business.</p><div class="meta-row"><span class="tag">Objectives</span><span class="stars">★★★★★</span></div><div class="bar"><span style="width:75%"></span></div><div class="stats"><div><b>7</b>Rules</div><div><b>5</b>Min read</div><div><b>2</b>Forms</div></div></article>
    <article class="card"><div class="card-img" role="img" aria-label="Photo of a retail owner in a store" style="background:linear-gradient(135deg,#e7cfc0,#c96a6a)"></div><h3>Common Reasons to Wait</h3><p>The most frequent issues that make a company not eligible, and how to fix them.</p><div class="meta-row"><span class="tag">Results</span><span class="stars">★★★★★</span></div><div class="bar"><span style="width:40%"></span></div><div class="stats"><div><b>6</b>Rules</div><div><b>4</b>Min read</div><div><b>0</b>Forms</div></div></article>
  </div>
</section>

<section class="discover" role="img" aria-label="Faded collage of community member portraits">
  <div class="wrap">
    <div class="discover-panel">
      <h2>Share clear compliance answers with your partners!</h2>
      <p>Want to learn more? See how it works</p>
    </div>
    <div class="connect-btn"><span class="name">Friendloop</span><span class="label">Connect with Friendloop</span></div>
  </div>
</section>

<section class="social">
  <h2>Connect with our social network :</h2>
  <div class="social-icons">
    <span style="background:#e44b3a"></span><span style="background:#d6452f"></span><span style="background:#e85a3d"></span><span style="background:#2d85c8"></span><span style="background:#c9302c"></span>
  </div>
</section>

<footer class="site-footer">
  <div class="wrap footer-cols">
    <div><h4>Get started</h4><ul><li>Company Questions</li><li>Eligibility Check</li><li>Objectives</li><li>Your Results</li><li>Sign Up</li></ul></div>
    <div><h4>Learn</h4><ul><li>Guides</li><li>Rule Basics</li><li>Glossary</li><li>FAQ</li><li>Blog</li></ul></div>
    <div><h4>Services</h4><ul><li>Legal Documents</li><li>Agreements</li><li>Filing Help</li><li>Pricing</li></ul></div>
    <div><h4>Partners</h4><ul><li>Affiliate Links</li><li>Law Firms</li><li>Accountants</li><li>Become a Partner</li></ul></div>
    <div><h4>About</h4><ul><li>What is MLAH?</li><li>Help &amp; Support</li><li>Terms of Use</li><li>Disclaimer</li><li>Privacy</li></ul></div>
  </div>
</footer>
<div class="bottom-bar">Copyright 2013 MLAH. All rights reserved.</div>

</body>
</html>
```